New Bicycle shop business card

Hi!
I'm looking for a business card for my new proffesional bike mechanics shop. This shop is only for fixing broken bikes and not selling bikes.
Peferbly a modern and sleek and modern design.
Colors: black, grey, red, white
Information:
Name: Rijwielwerkplaats Vanhoutte
Shop owner: Bart Vanhoutte & Marieke Segers
Website: www.rijwielwerkplaats-vanhoutte.be
Email: info@rijwielwerkplaats-vanhoutte.be
Phone number: +32471902368
Street adres: Kerkweg 46
9940 Bellebeke
Slogan/shop information: Herstellingen van alle merken.
Logo: see files.
Target Market(s)
People who seek a mechanic to fix or upgrade their bikes.
Contact Information for Business Card
Information:
Website: info@rijwielwerkplaats-vanhoutte.be
9940 Bellebeke
Logo: see files.

```html
<!DOCTYPE html>
<html lang="nl">
<head>
<meta charset="utf-8">
<title>Rijwielwerkplaats Vanhoutte – visitekaartje</title>
<link rel="stylesheet" href="https://fonts.googleapis.com/css2?family=Montserrat:wght@500;800&family=Roboto:wght@400&display=swap">
<style>
  :root{
    --ink:#222326;
    --ink-deep:#1a1b1d;
    --red:#e0303f;
    --grey:#9a9c9f;
    --white:#ffffff;
    --stage:#3a3b3d;
  }
  html,body{margin:0;padding:0;width:799px;height:1200px;overflow:hidden;background:var(--stage);}
  .sheet{position:relative;width:799px;height:1200px;}
  .card{
    position:absolute;left:80px;width:640px;height:366px;
    background:var(--ink);border-radius:22px;overflow:hidden;
    box-shadow:0 10px 30px rgba(0,0,0,.45);
  }
  .card--front{top:130px;}
  .card--back{top:690px;}

  .brand{font-family:"Montserrat",sans-serif;font-weight:800;color:var(--white);
    text-transform:uppercase;letter-spacing:1px;line-height:1.05;}
  .brand-dot{display:block;width:30px;height:30px;border-radius:50%;background:var(--red);}

  .front-brand{position:absolute;top:80px;left:0;right:0;text-align:center;}
  .front-brand .brand-dot{margin:0 auto 18px;}
  .front-brand .brand{font-size:34px;}
  .front-web{position:absolute;top:268px;left:0;right:0;text-align:center;
    font-family:"Roboto",sans-serif;font-size:17px;color:var(--white);}
  .front-web .accent{color:var(--red);}

  .waves{position:absolute;inset:0;}
  .back-brand{position:absolute;top:30px;left:34px;display:flex;align-items:center;gap:14px;}
  .back-brand .brand{font-size:22px;}
  .contact{position:absolute;top:112px;left:40px;margin:0;padding:0;list-style:none;
    font-family:"Roboto",sans-serif;font-size:14px;color:var(--white);}
  .contact li{display:flex;align-items:center;gap:10px;height:21px;}
  .contact li.plain{padding-left:0;}
  .contact svg{width:12px;height:12px;fill:var(--red);flex:none;}
  .holder{position:absolute;right:44px;bottom:34px;text-align:right;}
  .holder-name{font-family:"Montserrat",sans-serif;font-weight:800;font-size:24px;
    color:var(--white);text-transform:uppercase;letter-spacing:1px;}
  .holder-role{font-family:"Roboto",sans-serif;font-size:15px;color:var(--white);margin-top:4px;}
</style>
</head>
<body>
<main class="sheet">

  <section class="card card--front" aria-label="Voorkant">
    <div class="front-brand">
      <span class="brand-dot"></span>
      <div class="brand">Rijwielwerkplaats<br>Vanhoutte</div>
    </div>
    <div class="front-web">www.rijwielwerkplaats-<span class="accent">vanhoutte</span>.be</div>
  </section>

  <section class="card card--back" aria-label="Achterkant">
    <svg class="waves" viewBox="0 0 640 366" preserveAspectRatio="none" aria-hidden="true">
      <path d="M0 200 C120 215 170 300 330 268 C470 240 560 285 640 300 L640 366 L0 366 Z" fill="var(--red)"/>
      <path d="M0 196 C60 200 110 240 190 262 C280 285 360 250 470 262 C560 272 610 290 640 298 L640 288 C600 276 550 258 470 250 C360 240 280 270 190 248 C120 230 60 190 0 182 Z" fill="var(--grey)"/>
      <path d="M0 200 C70 210 120 250 200 270 C290 290 370 258 470 268 C560 278 610 296 640 304 L640 300 C610 292 560 274 470 262 C360 250 280 285 190 262 C110 240 60 200 0 196 Z" fill="var(--ink-deep)"/>
    </svg>

    <div class="back-brand">
      <span class="brand-dot"></span>
      <div class="brand">Rijwielwerkplaats<br>Vanhoutte</div>
    </div>

    <ul class="contact">
      <li><svg viewBox="0 0 24 24"><path d="M6.6 10.8a15 15 0 0 0 6.6 6.6l2.2-2.2a1 1 0 0 1 1-.25 11.4 11.4 0 0 0 3.6.57 1 1 0 0 1 1 1V20a1 1 0 0 1-1 1A17 17 0 0 1 3 4a1 1 0 0 1 1-1h3.5a1 1 0 0 1 1 1c0 1.25.2 2.45.57 3.6a1 1 0 0 1-.25 1z"/></svg>+32471902368</li>
      <li><svg viewBox="0 0 24 24"><path d="M2 5h20v14H2z M2 5l10 8 10-8" /></svg>www.rijwielwerkplaats-vanhoutte.be</li>
      <li><svg viewBox="0 0 24 24"><circle cx="12" cy="12" r="10"/></svg>info@rijwielwerkplaats-vanhoutte.be</li>
      <li class="plain">Kerkweg 46 9940 Bellebeke</li>
    </ul>

    <div class="holder">
      <div class="holder-name">Marieke Segers</div>
      <div class="holder-role">Owner</div>
    </div>
  </section>

</main>
</body>
</html>
```